Flyer Re-Design

We need a flyer re-design for a company that recently started doing it's own graphic design. Although we've taken a first attempt at the design, we would like a design professional, like yourself show us how much better you can do it. We're going through a re-branding as the logo reads "formerly" known as and although we'd like to keep the logo as it is---everything else should be more contemporary.

5.5" x 8.5" or 5" x 7"

Target Market(s)

Bahamas Youth

Industry/Entity Type

Graphic Design

Font styles to use
Sans Serif

Requirements
Must have
• Current Logo. Include as many details as already listed in the document.
Nice to have
• Fresh New, Crisp Ideas for this Pharmacy rebranding
Should not have
• Too Many colors or serif fonts

```html
<!DOCTYPE html>
<html lang="en">
<head>
<meta charset="UTF-8">
<title>Vital Bloom Pharmacy – Rewards Club Flyer</title>
<link rel="stylesheet" href="https://fonts.googleapis.com/css2?family=Fira+Sans:ital,wght@0,400;0,500;0,600;0,700;1,400;1,500;1,600;1,700&display=swap">
<style>
  :root {
    --backdrop: #e4e4e4;
    --paper: #ffffff;
    --brand-green: #2b7a3c;
    --brand-red: #b0191b;
    --ink: #2a2a2a;
    --bar-black: #151515;
    --bar-text: #a8dba0;
    --apple-light: #d6383a;
    --apple-dark: #6e0b10;
  }
  * { margin: 0; padding: 0; box-sizing: border-box; }
  html, body {
    width: 1200px; height: 1000px; overflow: hidden;
    background: var(--backdrop);
    font-family: "Fira Sans", Arial, sans-serif;
  }
  .flyer {
    position: absolute; left: 273px; top: 40px;
    width: 654px; height: 920px;
    background: var(--paper);
    box-shadow: 0 6px 18px rgba(0,0,0,0.12);
  }
  .brand {
    position: absolute; right: 107px; top: 22px;
    width: 210px;
  }
  .brand-name {
    display: flex; align-items: center; gap: 6px;
    color: var(--brand-red); font-weight: 600; font-size: 15px; letter-spacing: 0.2px;
  }
  .brand-dot { width: 14px; height: 14px; border-radius: 50%; background: var(--brand-green); flex: none; }
  .brand-contact {
    margin: 3px 0 0 20px; font-size: 7.5px; line-height: 9.5px; color: var(--ink);
  }
  .hero-photo {
    position: absolute; left: 77px; top: 103px; width: 267px; height: 258px;
    background: radial-gradient(circle at 50% 60%, var(--apple-light) 0%, var(--apple-dark) 45%, #ffffff 47%);
  }
  .headline {
    position: absolute; right: 95px; top: 180px;
    text-align: right; color: var(--brand-green);
    font-weight: 600; font-size: 46px; line-height: 54px; text-transform: uppercase;
  }
  .divider {
    position: absolute; left: 98px; top: 401px; width: 461px; height: 5px;
    background: var(--brand-red);
  }
  .perk {
    position: absolute; top: 443px; width: 112px; height: 112px; border-radius: 50%;
    background: var(--brand-green); color: #fff;
    display: flex; align-items: center; justify-content: center; text-align: center;
    font-style: italic; font-size: 13.5px; line-height: 16px; padding: 10px;
  }
  .perk--free { left: 49px; }
  .perk--points { left: 199px; }
  .perk--double { left: 346px; }
  .perk--refer { left: 494px; }
  .exclusives-title {
    position: absolute; left: 46px; top: 596px;
    color: var(--brand-red); font-weight: 700; font-style: italic; font-size: 42px;
    text-transform: uppercase; letter-spacing: 0.5px;
  }
  .exclusives-list {
    position: absolute; left: 46px; top: 660px; list-style: none;
    font-size: 14px; line-height: 20px; color: var(--ink);
  }
  .exclusives-list li::before {
    content: ""; display: inline-block; width: 5px; height: 5px; border-radius: 50%;
    background: var(--brand-green); margin: 0 7px 2px 0; vertical-align: middle;
  }
  .exclusives-list em { color: var(--brand-red); font-weight: 700; }
  .thanks {
    position: absolute; left: 337px; top: 608px; width: 300px;
    text-align: center; color: var(--brand-green);
    font-style: italic; font-weight: 600; font-size: 38px; line-height: 40px;
  }
  .thanks strong { color: var(--brand-red); font-weight: 700; text-transform: uppercase; }
  .web-link {
    position: absolute; left: 337px; top: 781px; width: 300px; text-align: center;
    font-size: 9px; font-style: italic; font-weight: 600; color: var(--ink);
  }
  .cta-bar {
    position: absolute; left: 38px; top: 822px; width: 578px; height: 38px;
    background: var(--bar-black); color: var(--bar-text);
    display: flex; align-items: center; justify-content: center;
    font-style: italic; font-weight: 600; font-size: 21px;
  }
  .footer-mark {
    position: absolute; right: 20px; top: 872px;
    display: flex; align-items: center; gap: 4px;
    color: var(--brand-red); font-weight: 600; font-size: 9px;
  }
  .footer-mark span { width: 9px; height: 9px; border-radius: 50%; background: var(--brand-green); }
</style>
</head>
<body>
  <main class="flyer">
    <header class="brand">
      <div class="brand-name"><span class="brand-dot"></span>Vital Bloom Pharmacy</div>
      <p class="brand-contact">12 Harbour View Drive, Coral Plaza<br>P.O. Box F-10234, Freeport, Grand Bahama, Bahamas<br>Tel: (242) 555 0148 Fax: (242) 555 0149</p>
    </header>

    <div class="hero-photo" role="img" aria-label="Photo of a shiny red apple with a green leaf"></div>

    <h1 class="headline">Join our<br>rewards<br>club now!</h1>

    <div class="divider"></div>

    <div class="perk perk--free">Absolutely free to join!</div>
    <div class="perk perk--points">You'll earn 1 point for every Dollar you spend</div>
    <div class="perk perk--double">Earn double points on selected items purchased</div>
    <div class="perk perk--refer">Earn 25 points when you refer a friend</div>

    <h2 class="exclusives-title">Exclusives</h2>
    <ul class="exclusives-list">
      <li>VIP access to our special events.</li>
      <li>Be the first to know about our specials.</li>
      <li>receive notice on non-advertised specials.</li>
      <li>Free subscription to our online newsletter.</li>
      <li>Free gift with sign up.</li>
      <li>Special <em>“members only”</em> shopping events</li>
    </ul>

    <p class="thanks">It’s Just<br>Our Way<br>of Saying<br><strong>Thank you.</strong></p>
    <p class="web-link">visit us at: www.vitalbloompharmacy.com</p>

    <div class="cta-bar">See Our Customer Service Representative Today!</div>

    <div class="footer-mark"><span></span>Vital Bloom</div>
  </main>
</body>
</html>
```